The Lantern Guild Pitchdeck Template

The Lantern Guild would like a branded pitch deck template design for members to use when presenting their projects and proposals. The deck should include 10-15 different slide designs, each with the same branded theme, but with a variety of icon graphics and other design features that will empower members to easily create a beautiful pitch deck just by adding written content.

Please visit lanternguildhq.org to get a sense for our branding - purple, space, galaxy, white font and the planetary logo are some commonalities.

Here are 2 google drive links with some additional designs

https://files.boxmeadow.net/share/f/8QzrTa2Lk5VbNw7cHyP0dJe3sUmXg4RiF

https://files.boxmeadow.net/share/f/3Kd9-Rm6Tq2-yLvBn051fopwxhcT_zj7

```html
<!DOCTYPE html>
<html lang="en">
<head>
<meta charset="utf-8">
<title>The Lantern Guild — Pitch Deck Template</title>
<link rel="stylesheet" href="https://fonts.googleapis.com/css2?family=Raleway:wght@400;500;600;700;800&display=swap">
<style>
:root{
  --canvas:#b3b3b6;
  --night:#150d26;
  --deep:#24143d;
  --plum:#3d2160;
  --violet:#7a2fa0;
  --magenta:#b23fd0;
  --orchid:#d58cf0;
  --mist:#cdbfe0;
  --white:#ffffff;
  --soft:rgba(255,255,255,.78);
}
*{box-sizing:border-box;margin:0;padding:0}
html,body{width:1200px;height:3458px;overflow:hidden}
body{background:var(--canvas);font-family:"Raleway",sans-serif;color:var(--white);position:relative}
.slide{position:absolute;width:554px;height:312px;overflow:hidden;background:var(--night)}
.col-a{left:32px}.col-b{left:616px}
.photo{position:absolute;inset:0}
.abs{position:absolute}
.brand{position:absolute;top:30px;right:20px;display:flex;align-items:center;gap:5px;font-size:9px;font-weight:700;color:var(--white);letter-spacing:.02em}
.brand-dot{width:12px;height:12px;border-radius:50%;border:2px solid var(--white)}
.h{font-weight:800;font-size:15px;letter-spacing:.01em;text-transform:uppercase}
.p{font-size:6.5px;line-height:1.45;color:var(--soft);font-weight:500}
.ct{font-size:9px;font-weight:700}
.num{display:inline-flex;width:11px;height:11px;border-radius:50%;background:var(--magenta);font-size:6px;align-items:center;justify-content:center;margin-right:14px;font-weight:700}
.toc li{list-style:none;font-size:8.5px;color:var(--soft);height:20.5px;display:flex;align-items:center;border-bottom:1px solid rgba(255,255,255,.12);width:190px}
.thumb{position:absolute;border-radius:2px}
.center{text-align:center}
.ring{position:absolute;border-radius:50%;border:3px solid var(--violet)}
.stat{position:absolute;width:76px;height:76px;border-radius:50%;background:var(--violet);box-shadow:0 0 0 4px rgba(178,63,208,.35);display:flex;align-items:center;justify-content:center;font-weight:800;font-size:18px}
.ico{position:absolute;width:24px;height:24px;border-radius:50%;background:var(--violet);box-shadow:0 0 0 3px rgba(178,63,208,.3)}
.card{position:absolute;width:90px;height:145px;border:1px solid rgba(255,255,255,.25);background:rgba(60,30,90,.35);border-radius:3px;text-align:center;padding:10px 7px}
.card .ico{position:static;display:block;margin:0 auto 8px}
.glass{position:absolute;border:1px solid rgba(255,255,255,.3);background:rgba(150,110,200,.22);border-radius:6px}
table{border-collapse:collapse;width:100%}
td,th{font-size:6.5px;text-align:left;padding:6px 8px;border-bottom:1px solid rgba(255,255,255,.12);color:var(--soft);font-weight:500}
th{color:var(--white);font-weight:700}
.pink{color:var(--magenta)}
.bar{position:absolute;bottom:56px;width:30px;background:rgba(50,30,70,.85)}
.bar i{position:absolute;left:0;right:0;bottom:0;background:var(--magenta);font-style:normal;font-size:6px;font-weight:700;display:flex;align-items:flex-end;justify-content:center;padding-bottom:3px}
.hex{position:absolute;width:100px;height:110px;clip-path:polygon(50% 0,100% 25%,100% 75%,50% 100%,0 75%,0 25%);display:flex;flex-direction:column;align-items:center;justify-content:center;text-align:center;padding:0 14px}
.icons svg{position:absolute;width:34px;height:34px;stroke:var(--white);fill:none;stroke-width:1.6}
</style>
</head>
<body>

<!-- 1 Title -->
<section class="slide col-a" style="top:32px">
  <div class="photo" role="img" aria-label="Traveller standing on a rock under a violet starry sky" style="background:radial-gradient(ellipse at 50% 20%,#6a4a95,#3a2260 45%,#1b0f30)"></div>
  <div class="brand" style="left:0;right:0;top:82px;justify-content:center">The Lantern Guild</div>
  <h1 class="h abs center" style="left:0;right:0;top:138px;font-size:23px">Presentation Title Here</h1>
  <p class="abs center" style="left:0;right:0;top:166px;font-size:6.5px;letter-spacing:1.2em;font-weight:600">SUBTITLE GOES HERE</p>
</section>

<!-- 2 Table of content -->
<section class="slide col-b" style="top:32px">
  <div class="photo" role="img" aria-label="Nebula over rippled violet sand dunes" style="background:linear-gradient(180deg,#7b4aa8,#402468 40%,#6b4a8a 75%,#2c1a48)"></div>
  <div class="brand">The Lantern Guild</div>
  <h2 class="h abs" style="left:362px;top:66px;font-size:14px">Table of Content</h2>
  <ul class="toc abs" style="left:340px;top:92px">
    <li><span class="num">1</span>Introduction</li>
    <li><span class="num">2</span>About Us</li>
    <li><span class="num">3</span>Welcome Message</li>
    <li><span class="num">4</span>Our Services</li>
    <li><span class="num">5</span>Our Team</li>
    <li><span class="num">6</span>Infographic</li>
    <li><span class="num">7</span>Chart</li>
    <li><span class="num">8</span>Table</li>
    <li><span class="num">9</span>Contact Us</li>
  </ul>
</section>

<!-- 3 Introduction -->
<section class="slide col-a" style="top:373px">
  <div class="photo" role="img" aria-label="Desert night landscape with a planet reflected in a giant eye" style="background:radial-gradient(circle at 68% 45%,#8a7aa8 0,#4b2d70 22%,#2a1845 55%,#160c28)"></div>
  <div class="brand" style="left:40px;right:auto;top:36px">The Lantern Guild</div>
  <h2 class="h abs" style="left:40px;top:106px;font-size:14px">Introduction</h2>
  <p class="p abs" style="left:40px;top:130px;width:222px;text-align:justify">Lorem ipsum dolor sit amet, consectetuer adipiscing elit, sed diam nonummy nibh euismod tincidunt ut laoreet dolore magna aliquam erat volutpat. Ut wisi enim ad minim veniam, quis nostrud exerci tation ullamcorper suscipit lobortis nisl ut aliquip ex ea commodo consequat. Duis autem vel eum iriure dolor in hendrerit in vulputate velit esse molestie consequat, vel illum dolore eu feugiat nulla facilisis.</p>
</section>

<!-- 4 Three content -->
<section class="slide col-b" style="top:373px">
  <div class="photo" style="background:radial-gradient(ellipse at 50% 30%,#4e2b7a,#251440 60%,#180d2b)"></div>
  <div class="brand">The Lantern Guild</div>
  <h2 class="h abs" style="left:40px;top:30px">Your Title Here</h2>
  <div class="thumb" role="img" aria-label="Fiery star surface" style="left:94px;top:84px;width:91px;height:91px;background:radial-gradient(#f0b070,#a04a3a 50%,#3a1a30)"></div>
  <div class="thumb" role="img" aria-label="Swirling galaxy over landscape" style="left:239px;top:84px;width:91px;height:91px;background:radial-gradient(#f0c0d8,#b06a9a 45%,#4a2a50)"></div>
  <div class="thumb" role="img" aria-label="Glowing pink nebula" style="left:385px;top:84px;width:91px;height:91px;background:radial-gradient(#f6c6ff,#b040d0 30%,#2a1040 70%)"></div>
  <div class="abs center" style="left:80px;top:188px;width:120px"><p class="ct">Content Title</p><p class="p" style="margin-top:5px">Lorem ipsum dolor sit amet, consectetuer adipiscing e lit, sed diam nonummy nibh euismod tincidunt ut laoreet dolore magna aliquam erat</p></div>
  <div class="abs center" style="left:225px;top:188px;width:120px"><p class="ct">Content Title</p><p class="p" style="margin-top:5px">Lorem ipsum dolor sit amet, consectetuer adipiscing e lit, sed diam nonummy nibh euismod tincidunt ut laoreet dolore magna aliquam erat</p></div>
  <div class="abs center" style="left:371px;top:188px;width:120px"><p class="ct">Content Title</p><p class="p" style="margin-top:5px">Lorem ipsum dolor sit amet, consectetuer adipiscing e lit, sed diam nonummy nibh euismod tincidunt ut laoreet dolore magna aliquam erat</p></div>
</section>

<!-- 5 Stacked images -->
<section class="slide col-a" style="top:714px">
  <div class="photo" role="img" aria-label="Pink and violet star field" style="background:radial-gradient(ellipse at 70% 40%,#5a2a70,#2a1240 50%,#150a25)"></div>
  <div class="brand">The Lantern Guild</div>
  <div class="thumb" role="img" aria-label="Misty mountain peaks" style="left:40px;top:102px;width:68px;height:150px;background:linear-gradient(#a89ac0,#6a5a8a)"></div>
  <div class="thumb" role="img" aria-label="Hand holding a glowing crystal" style="left:117px;top:50px;width:68px;height:150px;background:linear-gradient(#2a3a70,#7a5ab0,#1a1840)"></div>
  <div class="thumb" role="img" aria-label="Colourful nebula" style="left:193px;top:102px;width:68px;height:150px;background:radial-gradient(#80a0ff,#a040a0 50%,#2a1040)"></div>
  <p class="abs" style="left:62px;top:239px;font-size:6.5px;font-weight:700">Title 1</p>
  <p class="abs" style="left:139px;top:187px;font-size:6.5px;font-weight:700">Title 2</p>
  <p class="abs" style="left:218px;top:239px;font-size:6.5px;font-weight:700">Title 3</p>
  <h2 class="h abs" style="left:315px;top:108px">Your Title Here</h2>
  <p class="p abs" style="left:315px;top:132px;width:195px">Lorem ipsum dolor sit amet, consectetuer adipiscing elit, sed diam nonummy nibh euismod tincidunt ut laoreet dolore magna aliquam erat volutpat. Ut wisi enim ad minim veniam, quis nostrud exerci tation ullamcorper suscipit lobortis</p>
</section>

<!-- 6 Circles on white -->
<section class="slide col-b" style="top:714px;background:var(--white)">
  <div class="abs" role="img" aria-label="Rocky violet landscape" style="left:0;top:0;width:554px;height:162px;background:linear-gradient(180deg,#3a2450,#5a3a72 70%,#2a183a)"></div>
  <div class="brand">The Lantern Guild</div>
  <h2 class="h abs" style="left:32px;top:36px">Your Title Here</h2>
  <p class="p abs" style="left:32px;top:58px;width:420px">Lorem ipsum dolor sit amet, consectetuer adipiscing elit, sed diam nonummy nibh euismod tincidunt ut laoreet dolore magna aliquam erat volutpat. Ut wisi enim ad minim veniam, quis nostrud exerci tation ullamcorper suscipit lobortis nisl ut aliquip ex ea commodo consequat. Duis autem vel eum iriure dolor in</p>
  <div class="ring" role="img" aria-label="Moonlit mountain scene" style="left:95px;top:113px;width:90px;height:90px;background:radial-gradient(#b0a0d8,#5a3a8a 70%)"></div>
  <div class="ring" role="img" aria-label="Planet horizon" style="left:241px;top:113px;width:90px;height:90px;background:radial-gradient(#d0c8e8,#6a5098 70%)"></div>
  <div class="ring" role="img" aria-label="Surreal sky scene" style="left:386px;top:113px;width:90px;height:90px;background:radial-gradient(#c8bce8,#7a60b0 70%)"></div>
  <div class="abs center" style="left:80px;top:215px;width:120px;color:var(--night)"><p class="ct">Content Title</p><p class="p" style="color:#444;margin-top:5px">Lorem ipsum dolor sit amet, consectetuer</p></div>
  <div class="abs center" style="left:226px;top:215px;width:120px;color:var(--night)"><p class="ct">Content Title</p><p class="p" style="color:#444;margin-top:5px">Lorem ipsum dolor sit amet, consectetuer</p></div>
  <div class="abs center" style="left:371px;top:215px;width:120px;color:var(--night)"><p class="ct">Content Title</p><p class="p" style="color:#444;margin-top:5px">Lorem ipsum dolor sit amet, consectetuer</p></div>
</section>

<!-- 7 Section -->
<section class="slide col-a" style="top:1055px">
  <div class="photo" role="img" aria-label="Misty rock arch with a lone figure" style="background:radial-gradient(ellipse at 65% 45%,#6a5a82,#3c2c58 50%,#221838)"></div>
  <p class="abs" style="left:40px;top:172px;font-size:30px;font-weight:800">01</p>
  <h2 class="h abs" style="left:40px;top:224px;font-size:14px">Section Title Here</h2>
  <p class="p abs" style="left:40px;top:246px;width:260px">Lorem ipsum dolor sit amet, consectetuer adipiscing elit, sed diam nonummy nibh euismod tincidunt ut laoreet dolore</p>
</section>

<!-- 8 Timeline -->
<section class="slide col-b" style="top:1055px">
  <div class="photo" role="img" aria-label="Deep space with planets" style="background:radial-gradient(ellipse at 50% 55%,#5a2a80,#2c1850 50%,#140a26)"></div>
  <div class="brand">The Lantern Guild</div>
  <h2 class="h abs" style="left:32px;top:40px">Timeline</h2>
  <div class="abs" style="left:40px;right:40px;top:155px;height:1px;background:linear-gradient(90deg,transparent,var(--orchid),transparent)"></div>
  <div class="abs" style="left:0;right:0;top:118px">
    <div class="abs center" style="left:51px;width:80px"><p class="ct">20YY</p><span class="abs" style="left:36px;top:33px;width:8px;height:8px;border-radius:50%;background:var(--white);box-shadow:0 0 10px 4px var(--magenta)"></span><p class="p" style="margin-top:50px">Lorem ipsum dolor sit amet, consectetuer adipiscing e lit, sed diam</p></div>
    <div class="abs center" style="left:141px;width:80px"><p class="ct">20YY</p><span class="abs" style="left:36px;top:33px;width:8px;height:8px;border-radius:50%;background:var(--white);box-shadow:0 0 10px 4px var(--magenta)"></span><p class="p" style="margin-top:50px">Lorem ipsum dolor sit amet, consectetuer adipiscing e lit, sed diam</p></div>
    <div class="abs center" style="left:230px;width:80px"><p class="ct">20YY</p><span class="abs" style="left:36px;top:33px;width:8px;height:8px;border-radius:50%;background:var(--white);box-shadow:0 0 10px 4px var(--magenta)"></span><p class="p" style="margin-top:50px">Lorem ipsum dolor sit amet, consectetuer adipiscing e lit, sed diam</p></div>
    <div class="abs center" style="left:320px;width:80px"><p class="ct">20YY</p><span class="abs" style="left:36px;top:33px;width:8px;height:8px;border-radius:50%;background:var(--white);box-shadow:0 0 10px 4px var(--magenta)"></span><p class="p" style="margin-top:50px">Lorem ipsum dolor sit amet, consectetuer adipiscing e lit, sed diam</p></div>
    <div class="abs center" style="left:410px;width:80px"><p class="ct">20YY</p><span class="abs" style="left:36px;top:33px;width:8px;height:8px;border-radius:50%;background:var(--white);box-shadow:0 0 10px 4px var(--magenta)"></span><p class="p" style="margin-top:50px">Lorem ipsum dolor sit amet, consectetuer adipiscing e lit, sed diam</p></div>
  </div>
</section>

<!-- 9 Icon list -->
<section class="slide col-a" style="top:1396px">
  <div class="photo" role="img" aria-label="Moon and meteors above dark mountains" style="background:radial-gradient(circle at 45% 35%,#9a90b0 0,#4a3a6a 18%,#2a1a48 50%,#160c28)"></div>
  <div class="brand">The Lantern Guild</div>
  <h2 class="h abs" style="left:38px;top:36px">Your Title Here</h2>
  <div class="abs" style="left:38px;top:78px;width:260px">
    <div style="position:relative;height:56px"><span class="ico" style="left:0;top:2px"></span><p class="p" style="margin-left:40px"><b style="color:#fff">Lorem ipsum dolor sit</b><br>Lorem ipsum dolor sit amet, consectetuer adipiscing elit, sed diam nonummy nibh euismod tincidunt ut laoreet dolore magna aliquam</p></div>
    <div style="position:relative;height:56px"><span class="ico" style="left:0;top:2px"></span><p class="p" style="margin-left:40px"><b style="color:#fff">Lorem ipsum dolor sit</b><br>Lorem ipsum dolor sit amet, consectetuer adipiscing elit, sed diam nonummy nibh euismod tincidunt ut laoreet dolore magna aliquam</p></div>
    <div style="position:relative;height:56px"><span class="ico" style="left:0;top:2px"></span><p class="p" style="margin-left:40px"><b style="color:#fff">Lorem ipsum dolor sit</b><br>Lorem ipsum dolor sit amet, consectetuer adipiscing elit, sed diam nonummy nibh euismod tincidunt ut laoreet dolore magna aliquam</p></div>
    <div style="position:relative;height:56px"><span class="ico" style="left:0;top:2px"></span><p class="p" style="margin-left:40px"><b style="color:#fff">Lorem ipsum dolor sit</b><br>Lorem ipsum dolor sit amet, consectetuer adipiscing elit, sed diam nonummy nibh euismod tincidunt ut laoreet dolore magna aliquam</p></div>
  </div>
</section>

<!-- 10 Bullets -->
<section class="slide col-b" style="top:1396px">
  <div class="photo" role="img" aria-label="Large ringed planet in dark space" style="background:radial-gradient(circle at 110% 40%,#6a4a78 0,#3c2450 30%,#1e1030 55%,#120a20)"></div>
  <div class="brand">The Lantern Guild</div>
  <h2 class="h abs" style="left:36px;top:40px">Your Title Here</h2>
  <p class="abs" style="left:36px;top:92px;font-size:9px;font-weight:700;line-height:1.4">Lorem Ipsum Dolor Sit Amet, Consectetuer<br>Adipiscing Elit, Sed Diam</p>
  <ul class="abs p" style="left:48px;top:130px;width:240px">
    <li style="margin-bottom:9px">Lorem ipsum dolor sit amet, consectetuer adipiscing elit, sed diam nonummy nibh euismod tincidunt ut laoreet dolore magna aliquam</li>
    <li style="margin-bottom:9px">Lorem ipsum dolor sit amet, consectetuer adipiscing elit, sed diam nonummy nibh euismod tincidunt ut laoreet dolore magna aliquam</li>
    <li style="margin-bottom:9px">Lorem ipsum dolor sit amet, consectetuer adipiscing elit, sed diam nonummy nibh euismod tincidunt ut laoreet dolore magna aliquam</li>
    <li style="margin-bottom:9px">Lorem ipsum dolor sit amet, consectetuer adipiscing elit, sed diam nonummy nibh euismod tincidunt ut laoreet dolore magna aliquam</li>
    <li>Lorem ipsum dolor sit amet, consectetuer adipiscing elit, sed diam nonummy nibh euismod tincidunt ut laoreet dolore magna aliquam</li>
  </ul>
</section>

<!-- 11 Stats -->
<section class="slide col-a" style="top:1737px">
  <div class="photo" role="img" aria-label="Giant space elevator rising from a misty horizon" style="background:linear-gradient(180deg,#1a0e2a,#3a2250 55%,#5a3a70 75%,#1a0e28)"></div>
  <div class="brand">The Lantern Guild</div>
  <h2 class="h abs" style="left:38px;top:36px">Your Title Here</h2>
  <div class="stat" style="left:54px;top:115px">100M</div>
  <div class="stat" style="left:181px;top:115px">200M</div>
  <div class="stat" style="left:309px;top:115px">500M</div>
  <div class="stat" style="left:430px;top:115px">800M</div>
  <p class="p abs" style="left:48px;top:222px;width:95px"><b style="color:#fff">Lorem ipsum dolor sitciv</b><br><br>Lorem ipsum dolor sitcivi amet, consectetuer adipis elit, sed diam nonummy h euismod tincidunt ut</p>
  <p class="p abs" style="left:176px;top:222px;width:95px"><b style="color:#fff">Lorem ipsum dolor sitciv</b><br><br>Lorem ipsum dolor sitcivi amet, consectetuer adipis elit, sed diam nonummy h euismod tincidunt ut</p>
  <p class="p abs" style="left:304px;top:222px;width:95px"><b style="color:#fff">Lorem ipsum dolor sitciv</b><br><br>Lorem ipsum dolor sitcivi amet, consectetuer adipis elit, sed diam nonummy h euismod tincidunt ut</p>
  <p class="p abs" style="left:425px;top:222px;width:95px"><b style="color:#fff">Lorem ipsum dolor sitciv</b><br><br>Lorem ipsum dolor sitcivi amet, consectetuer adipis elit, sed diam nonummy h euismod tincidunt ut</p>
</section>

<!-- 12 Cards -->
<section class="slide col-b" style="top:1737px">
  <div class="photo" role="img" aria-label="Earth-like planet rising in starry space" style="background:radial-gradient(ellipse at 58% 100%,#8a9ab8 0,#3a4a70 30%,#1a1430 55%,#100a1c)"></div>
  <div class="brand">The Lantern Guild</div>
  <h2 class="h abs" style="left:36px;top:34px">Your Title Here</h2>
  <p class="p abs" style="left:36px;top:58px;width:220px">Lorem ipsum dolor sit amet, consectetuer adipiscing elit, sed diam nonummy nibh euismod tincidunt ut laoreet dolore magna</p>
  <div class="card" style="left:88px;top:120px"><span class="ico"></span><p class="ct" style="font-size:6.5px">Lorem ipsum dolor sit</p><p class="p" style="margin-top:8px">Lorem ipsum dolor sit amet, consectetuer adipiscing elit, sed diam nonummy nibh euismod tincidunt ut laoreet dolore magna aliquam erat</p></div>
  <div class="card" style="left:222px;top:120px"><span class="ico"></span><p class="ct" style="font-size:6.5px">Lorem ipsum dolor sit</p><p class="p" style="margin-top:8px">Lorem ipsum dolor sit amet, consectetuer adipiscing elit, sed diam nonummy nibh euismod tincidunt ut laoreet dolore magna aliquam erat</p></div>
  <div class="card" style="left:356px;top:120px"><span class="ico"></span><p class="ct" style="font-size:6.5px">Lorem ipsum dolor sit</p><p class="p" style="margin-top:8px">Lorem ipsum dolor sit amet, consectetuer adipiscing elit, sed diam nonummy nibh euismod tincidunt ut laoreet dolore magna aliquam erat</p></div>
</section>

<!-- 13 Glass text -->
<section class="slide col-a" style="top:2078px">
  <div class="photo" role="img" aria-label="Astronaut on a shore beneath a glowing violet sky" style="background:radial-gradient(circle at 44% 45%,#e8d8ff 0,#8a60c0 8%,#4a2a78 35%,#1a0e2c 80%)"></div>
  <div class="brand">The Lantern Guild</div>
  <h2 class="h abs" style="left:38px;top:36px">Your Title Here</h2>
  <p class="abs" style="left:38px;top:110px;font-size:7px;font-weight:700">Lorem Ipsum Dolor<br>Sit Amet, Consectetuer Adipiscing Elit,</p>
  <p class="p abs" style="left:38px;top:136px;width:168px">Lorem ipsum dolor sit amet, consectetuer adipiscing elit, sed diam nonummy nibh euismod tincidunt ut laoreet dolore magna aliquam erat volutpat. Ut wisi enim ad minim veniam, quis nostrud exerci tation ullamcorper suscipit lobortis nisl ut aliquip ex ea commodo consequat. Duis autem vel eum iriure</p>
  <div class="glass" style="left:276px;top:70px;width:248px;height:186px;padding:14px 16px">
    <p style="font-size:7px;font-weight:700">Lorem Ipsum Dolor<br>Sit Amet, Consectetuer Adipiscing Elit, Sed Diam</p>
    <p class="p" style="margin-top:7px">Lorem ipsum dolor sit amet, consectetuer adipiscing elit, sed diam nonummy nibh euismod tincidunt ut laoreet dolore magna aliquam erat volutpat. Ut wisi enim ad minim veniam, quis nostrud exerci tation ullamcorper suscipit lobortis nisl ut aliquip ex ea commodo consequat.</p>
    <p class="p" style="margin-top:7px">Duis autem vel eum iriure dolor in hendrerit in vulputate velit esse molestie consequat, vel illum dolore eu feugiat nulla facilisis at vero eros et accumsan et iusto odio dignissim qui blandit praesent luptatum zzril delenit augue duis dolore te feugait nulla facilisi.</p>
    <p class="p" style="margin-top:7px">Lorem ipsum dolor sit amet, cons ectetuer adipiscing elit, sed diam nonummy nibh euismod tincidunt ut laoreet dolore magna</p>
  </div>
</section>

<!-- 14 Table -->
<section class="slide col-b" style="top:2078px">
  <div class="photo" style="background:radial-gradient(ellipse at 50% 50%,#3a2458,#1e1234 60%,#140a24)"></div>
  <div class="brand">The Lantern Guild</div>
  <h2 class="h abs" style="left:32px;top:36px">Table Slide</h2>
  <div class="glass" style="left:92px;top:90px;width:394px;height:190px;padding:12px 8px;background:rgba(70,45,100,.45)">
    <p style="font-size:6.5px;font-weight:700;margin:6px 8px 10px">Lorem ipsum dolor sit amet, consectetuer adipiscing elit, sed diam</p>
    <table>
      <tr><th>Lorem</th><th>Lorem ipsum</th><th>Lorem</th><th>Lorem</th></tr>
      <tr><td>Lorem ipsum</td><td>Lorem ipsum dolor sit amet, consectetuer</td><td>123</td><td class="pink">123</td></tr>
      <tr><td>Lorem ipsum</td><td>Lorem ipsum dolor sit amet, consectetuer</td><td>123</td><td class="pink">123</td></tr>
      <tr><td>Lorem ipsum</td><td>Lorem ipsum dolor sit amet, consectetuer</td><td>123</td><td class="pink">123</td></tr>
      <tr><td>Lorem ipsum</td><td>Lorem ipsum dolor sit amet, consectetuer</td><td>123</td><td class="pink">123</td></tr>
      <tr><td>Lorem ipsum</td><td>Lorem ipsum dolor sit amet, consectetuer</td><td>123</td><td class="pink">123</td></tr>
    </table>
  </div>
</section>

<!-- 15 Chart -->
<section class="slide col-a" style="top:2419px">
  <div class="photo" role="img" aria-label="Tree silhouette under a purple aurora" style="background:linear-gradient(180deg,#2a1840,#4a2a68 55%,#7a4a98 80%,#1e1030)"></div>
  <div class="brand">The Lantern Guild</div>
  <h2 class="h abs" style="left:40px;top:94px;font-size:14px">Chart Slide</h2>
  <p class="p abs" style="left:40px;top:140px;width:168px">Lorem ipsum dolor sit amet, consectetuer adipiscing elit, sed diam nonummy nibh euismod tincidunt ut laoreet dolore magna aliquam erat volutpat. Ut wisi enim ad minim veniam, quis nostrud exerci tation ullamcorper suscipit lobortis nisl ut aliquip ex ea commodo consequat. Duis autem vel eum iriure dolor in hendrerit in vulputate velit esse molestie consequat, vel illum dolore eu feugiat nulla facilisis at vero eros et</p>
  <div class="bar" style="left:265px;height:140px"><i style="height:14px">20%</i></div>
  <div class="bar" style="left:309px;height:140px"><i style="height:42px">30%</i></div>
  <div class="bar" style="left:352px;height:140px"><i style="height:63px">45%</i></div>
  <div class="bar" style="left:396px;height:140px"><i style="height:70px">50%</i></div>
  <div class="bar" style="left:440px;height:140px"><i style="height:84px">60%</i></div>
  <div class="bar" style="left:483px;height:140px"><i style="height:112px">80%</i></div>
</section>

<!-- 16 Orbit infographic -->
<section class="slide col-b" style="top:2419px">
  <div class="photo" role="img" aria-label="Violet nebula with a dark planet" style="background:radial-gradient(ellipse at 70% 40%,#5a3a80,#2e1a50 50%,#160c28)"></div>
  <div class="brand">The Lantern Guild</div>
  <h2 class="h abs center" style="left:0;right:0;top:36px;font-size:14px">Infographic</h2>
  <svg class="abs" style="left:80px;top:175px" width="400" height="120" viewBox="0 0 400 120" fill="none" stroke="rgba(255,255,255,.55)">
    <ellipse cx="200" cy="60" rx="190" ry="50"/><ellipse cx="200" cy="60" rx="140" ry="36"/><ellipse cx="200" cy="60" rx="90" ry="22"/>
  </svg>
  <span class="ico" style="left:98px;top:137px"></span>
  <span class="ico" style="left:265px;top:137px"></span>
  <span class="ico" style="left:437px;top:137px"></span>
  <span class="ico" style="left:176px;top:188px"></span>
  <span class="ico" style="left:352px;top:188px"></span>
  <p class="p abs center" style="left:62px;top:84px;width:96px"><b style="color:#fff">Lorem ipsum</b><br>Lorem ipsum dolor sit amet, consectetuer</p>
  <p class="p abs center" style="left:229px;top:84px;width:96px"><b style="color:#fff">Lorem ipsum</b><br>Lorem ipsum dolor sit amet, consectetuer</p>
  <p class="p abs center" style="left:400px;top:84px;width:96px"><b style="color:#fff">Lorem ipsum</b><br>Lorem ipsum dolor sit amet, consectetuer</p>
  <p class="p abs center" style="left:140px;top:142px;width:96px"><b style="color:#fff">Lorem ipsum</b><br>Lorem ipsum dolor sit amet, consectetuer</p>
  <p class="p abs center" style="left:316px;top:142px;width:96px"><b style="color:#fff">Lorem ipsum</b><br>Lorem ipsum dolor sit amet, consectetuer</p>
</section>

<!-- 17 Hexagons -->
<section class="slide col-a" style="top:2760px">
  <div class="photo" role="img" aria-label="Starry sky with a pale light beam" style="background:radial-gradient(ellipse at 60% 40%,#4a3070,#24163e 55%,#140a24)"></div>
  <div class="brand">The Lantern Guild</div>
  <h2 class="h abs" style="left:40px;top:40px;font-size:14px">Infographic</h2>
  <div class="hex" style="left:222px;top:50px;background:var(--violet)"><p class="ct" style="font-size:7px">Lorem</p><p class="p">Lorem ipsum dolor sit amet, consectetuer adipiscing elit, sed diam</p></div>
  <div class="hex" style="left:163px;top:150px;background:#4a2a9a"><p class="ct" style="font-size:7px">Lorem</p><p class="p">Lorem ipsum dolor sit amet, consectetuer adipiscing elit, sed diam</p></div>
  <div class="hex" style="left:281px;top:150px;background:#a0307a"><p class="ct" style="font-size:7px">Lorem</p><p class="p">Lorem ipsum dolor sit amet, consectetuer adipiscing elit, sed diam</p></div>
</section>

<!-- 18 Central circle -->
<section class="slide col-b" style="top:2760px">
  <div class="photo" role="img" aria-label="Road leading toward a purple cosmic horizon" style="background:radial-gradient(ellipse at 50% 20%,#4a2a78,#24143e 55%,#140a22)"></div>
  <div class="brand">The Lantern Guild</div>
  <h2 class="h abs center" style="left:0;right:0;top:40px;font-size:14px">Infographic</h2>
  <svg class="abs" style="left:130px;top:125px" width="300" height="110" viewBox="0 0 300 110" fill="none" stroke="rgba(255,255,255,.6)"><ellipse cx="150" cy="55" rx="146" ry="50"/></svg>
  <div class="abs center" style="left:217px;top:100px;width:120px;height:120px;border-radius:50%;background:var(--violet);box-shadow:0 0 0 8px rgba(178,63,208,.3);padding-top:46px"><p class="ct" style="font-size:7px">Lorem ipsum</p><p class="p" style="padding:0 12px">Lorem ipsum dolor sit amet, consectetuer adipiscing elit, sed diam nonummy nibh</p></div>
  <span class="ico" style="left:158px;top:120px;background:#7a3aa8"></span>
  <span class="ico" style="left:378px;top:120px;background:#3a2a90"></span>
  <span class="ico" style="left:174px;top:182px;background:#e07a3a;box-shadow:0 0 0 3px rgba(224,122,58,.3)"></span>
  <span class="ico" style="left:362px;top:182px;background:#e8b830;box-shadow:0 0 0 3px rgba(232,184,48,.3)"></span>
  <p class="p abs" style="left:32px;top:108px;width:100px;text-align:right"><b style="color:#fff">Lorem ipsum</b><br>Lorem ipsum dolor sit amet, consectetuer adipiscing elit.</p>
  <p class="p abs" style="left:62px;top:185px;width:100px;text-align:right"><b style="color:#fff">Lorem ipsum</b><br>Lorem ipsum dolor sit amet, consectetuer adipiscing elit.</p>
  <p class="p abs" style="left:423px;top:108px;width:100px"><b style="color:#fff">Lorem ipsum</b><br>Lorem ipsum dolor sit amet, consectetuer adipiscing elit.</p>
  <p class="p abs" style="left:400px;top:185px;width:100px"><b style="color:#fff">Lorem ipsum</b><br>Lorem ipsum dolor sit amet, consectetuer adipiscing elit.</p>
</section>

<!-- 19 Icons -->
<section class="slide col-a icons" style="top:3101px">
  <div class="photo" role="img" aria-label="Spiral galaxy in deep purple space" style="background:radial-gradient(ellipse at 30% 60%,#6a3a90,#2c1850 45%,#140a24)"></div>
  <h2 class="h abs center" style="left:0;right:0;top:40px;font-size:14px">Free Icons</h2>
  <svg style="left:44px;top:100px" viewBox="0 0 34 34"><circle cx="17" cy="17" r="8"/><ellipse cx="17" cy="17" rx="15" ry="5"/></svg>
  <svg style="left:99px;top:100px" viewBox="0 0 34 34"><path d="M8 30V5l16 5-16 6"/><circle cx="24" cy="26" r="4"/></svg>
  <svg style="left:154px;top:100px" viewBox="0 0 34 34"><path d="M8 26l18-18M12 30l-6-6 12-12 6 6z"/></svg>
  <svg style="left:209px;top:100px" viewBox="0 0 34 34"><ellipse cx="17" cy="20" rx="14" ry="5"/><path d="M9 18a8 8 0 0 1 16 0"/></svg>
  <svg style="left:264px;top:100px" viewBox="0 0 34 34"><rect x="9" y="10" width="16" height="14" rx="3"/><path d="M17 10V5M12 30v-6M22 30v-6"/></svg>
  <svg style="left:319px;top:100px" viewBox="0 0 34 34"><circle cx="17" cy="17" r="12"/><rect x="10" y="13" width="14" height="8" rx="3"/></svg>
  <svg style="left:374px;top:100px" viewBox="0 0 34 34"><circle cx="17" cy="17" r="7"/><path d="M17 3v5M17 26v5M3 17h5M26 17h5M7 7l4 4M23 23l4 4M27 7l-4 4M7 27l4-4"/></svg>
  <svg style="left:429px;top:100px" viewBox="0 0 34 34"><path d="M6 28h22M17 28V14M8 10h18l-3 4H11z"/></svg>
  <svg style="left:44px;top:158px" viewBox="0 0 34 34"><path d="M9 28V14a8 8 0 0 1 16 0v14M5 28h24"/></svg>
  <svg style="left:99px;top:158px" viewBox="0 0 34 34"><path d="M17 17a3 3 0 1 1 3 3 7 7 0 1 1-8-8 11 11 0 1 1 12 12"/></svg>
  <svg style="left:154px;top:158px" viewBox="0 0 34 34"><circle cx="17" cy="17" r="12"/><path d="M6 13h22M5 19h24"/></svg>
  <svg style="left:209px;top:158px" viewBox="0 0 34 34"><path d="M6 16l20-8 2 5-20 8zM14 20l-6 10M18 19l6 11"/></svg>
  <svg style="left:264px;top:158px" viewBox="0 0 34 34"><ellipse cx="17" cy="22" rx="14" ry="5"/><path d="M10 20a7 7 0 0 1 14 0"/></svg>
  <svg style="left:319px;top:158px" viewBox="0 0 34 34"><circle cx="17" cy="17" r="12"/><circle cx="17" cy="17" r="7"/></svg>
  <svg style="left:374px;top:158px" viewBox="0 0 34 34"><circle cx="11" cy="23" r="6"/><path d="M15 19l14-14M18 24l12-8M10 16l8-12"/></svg>
  <svg style="left:429px;top:158px" viewBox="0 0 34 34"><rect x="12" y="12" width="10" height="10"/><path d="M3 17h9M22 17h9M17 3v9M17 22v9"/></svg>
  <svg style="left:44px;top:216px" viewBox="0 0 34 34"><circle cx="17" cy="17" r="12"/><circle cx="13" cy="13" r="2"/><circle cx="21" cy="21" r="3"/></svg>
  <svg style="left:99px;top:216px" viewBox="0 0 34 34"><circle cx="17" cy="17" r="12"/><path d="M8 9l18 16M10 27L26 9"/></svg>
  <svg style="left:154px;top:216px" viewBox="0 0 34 34"><path d="M6 14l18-7 2 5-18 7zM15 19v11M10 30h10"/></svg>
  <svg style="left:209px;top:216px" viewBox="0 0 34 34"><path d="M17 3c6 6 6 16 3 22h-6c-3-6-3-16 3-22zM14 25l-4 5M20 25l4 5"/></svg>
  <svg style="left:264px;top:216px" viewBox="0 0 34 34"><circle cx="17" cy="17" r="9"/><ellipse cx="17" cy="17" rx="15" ry="4"/></svg>
  <svg style="left:319px;top:216px" viewBox="0 0 34 34"><ellipse cx="17" cy="14" rx="12" ry="4"/><path d="M11 18l-4 12M23 18l4 12M17 18v12"/></svg>
  <svg style="left:374px;top:216px" viewBox="0 0 34 34"><circle cx="17" cy="17" r="12"/><path d="M10 14h8M12 20h10"/></svg>
  <svg style="left:429px;top:216px" viewBox="0 0 34 34"><circle cx="12" cy="17" r="7"/><path d="M19 14l6-3v12l-6-3M28 12a7 7 0 0 1 0 10"/></svg>
</section>

<!-- 20 Contact -->
<section class="slide col-b" style="top:3101px">
  <div class="photo" style="background:radial-gradient(ellipse at 50% 50%,#241838,#140c22 70%)"></div>
  <p class="abs center" style="left:0;right:0;top:82px;font-size:26px;font-weight:800;color:rgba(255,255,255,.22)">The Lantern Guild</p>
  <h2 class="h abs center" style="left:0;right:0;top:160px;font-size:22px">Contact Us</h2>
  <p class="abs center" style="left:0;right:0;top:190px;font-size:8.5px;letter-spacing:.12em;font-weight:500;color:var(--soft)">lanternguildhq.org</p>
</section>

</body>
</html>
```